Creation of an elegant and modern turnkey Shopify website

Hello,

We are a new company specializing in the sale of above-ground pools. We want to create a turnkey website, ideally using Shopify. For now, we need a "showcase" site, not an e-commerce platform, with four tabs:

Home Page (an overall presentation of the company)
Our Products (an overview of all the above-ground pools we sell)
Our Projects (a page inspired by Instagram to showcase photos of our future projects)
Contact (a page with all our contact information and a contact form)

We are looking to create a highly visual, elegant, and modern website with vibrant splashes of color. We will provide the text, photos (along with instructions on where to place them on each page), and all other necessary information as attachments.

Thank you in advance for your proposals!

The Brisa Lagoon Team

Target Market(s)

Targeted at Swiss customers (a translator will need to be installed for different languages)

Industry/Entity Type

Sale of customised above-ground pools

Coding

Coded - Design and coding required

Font styles to use
Sans Serif

Colors
0094D4
00A9DD
6FCCEA
C7EBF8
E9F6FB
00AB8E
00BBA5
67D7C9
C6EFE9
E9F9F6

Requirements
Must have
• A stunning, elegant and modern look
Nice to have
• Inspiration from the colors of our logo throughout the site, but in an elegant way
Should not have
• An overly classic look for swimming pool sites

```html
<!DOCTYPE html>
<html lang="en">
<head>
<meta charset="utf-8">
<title>Brisa Lagoon – Above-Ground Pools</title>
<link rel="stylesheet" href="https://fonts.googleapis.com/css2?family=Josefin+Sans:wght@300;400&family=Roboto:wght@400;500;700&display=swap">
<style>
:root{
  --teal:#0fa98e;
  --cyan:#19e3f5;
  --ink:#111;
  --text:#555;
  --line:#e2e2e2;
  --ice:#e4f9fb;
  --mist:#edf3fe;
  --fog:#f3f3f3;
  --white:#fff;
}
*{margin:0;padding:0;box-sizing:border-box}
html,body{width:1200px;height:3187px;overflow:hidden;background:var(--white)}
body{font-family:'Roboto',sans-serif;color:var(--ink);position:relative}
.abs{position:absolute}
.topbar{left:0;top:0;width:1200px;height:35px;background:var(--teal);color:var(--white);font-size:12px;font-weight:700;text-align:center;line-height:35px;letter-spacing:.1px}
.brand{left:0;width:1200px;top:52px;text-align:center;font-family:'Josefin Sans',sans-serif;font-weight:300;color:#3a3a3a;font-size:38px;line-height:42px;letter-spacing:1px}
.nav{left:142px;top:154px;width:922px;height:36px;border-bottom:2px solid var(--line)}
.nav-links{position:absolute;left:0;width:100%;top:6px;text-align:center;font-size:14px;font-weight:700;letter-spacing:.2px}
.nav-links span{margin:0 14px}
.nav svg{position:absolute}
.hero-photo{left:402px;top:220px;width:798px;height:496px;background:linear-gradient(160deg,#f6a21f 0%,#e88a2a 25%,#4a8ee0 50%,#2f6fc9 65%,#b5723f 85%,#8a4a25 100%)}
.hero-title{left:111px;top:338px;font-family:'Josefin Sans',sans-serif;font-weight:300;font-size:44px;line-height:64px;color:var(--ink);text-transform:uppercase;letter-spacing:-.5px}
.btn{background:var(--cyan);color:var(--ink);font-weight:700;font-size:14px;text-align:center;text-transform:uppercase}
.hero-btn{left:111px;top:542px;width:149px;height:44px;line-height:44px}
.slide-next{left:1074px;top:452px;width:44px;height:44px;border-radius:50%;background:var(--white);display:flex;align-items:center;justify-content:center}
.photo{position:absolute}
.panel{position:absolute;text-align:center;display:flex;flex-direction:column;align-items:center;justify-content:center}
.panel h2{font-size:20px;font-weight:700;line-height:29px;text-transform:uppercase;margin-bottom:22px}
.panel p{font-size:13.5px;line-height:25px;color:var(--text);max-width:360px}
.panel p b{color:var(--ink);font-weight:400}
.panel .btn{width:149px;height:44px;line-height:44px;margin-top:26px}
.contact-box{left:111px;top:1967px;width:978px;height:351px;background:var(--fog);text-align:center}
.serif-head{font-family:'Josefin Sans',sans-serif;font-weight:300;text-transform:uppercase;color:var(--ink)}
.contact-box h2{font-size:40px;margin-top:70px;letter-spacing:-.5px}
.contact-box p{width:600px;margin:24px auto 0;font-size:13.5px;line-height:25px;color:var(--text)}
.contact-box h3{font-size:30px;margin-top:42px;letter-spacing:-.5px}
.why{left:0;width:1200px;top:2390px;text-align:center;font-size:40px;letter-spacing:-.5px}
.card{position:absolute;top:2459px;width:318px;height:392px;background:var(--ice);text-align:center}
.card .photo{left:3px;top:0;width:312px;height:173px}
.card .badge{position:absolute;left:135px;top:193px;width:48px;height:48px;border-radius:50%;background:var(--white);display:flex;align-items:center;justify-content:center}
.card h4{position:absolute;top:262px;width:100%;font-size:16px;font-weight:500;text-transform:uppercase;letter-spacing:.3px}
.card p{position:absolute;top:292px;left:26px;width:266px;font-size:13.5px;line-height:26px;color:var(--text)}
.divider{left:111px;top:2890px;width:978px;height:1px;background:#cfcfcf}
.foot-brand{left:128px;top:2978px;font-family:'Josefin Sans',sans-serif;font-weight:300;font-size:36px;line-height:40px;color:#3a3a3a;text-align:center}
.foot-col h5{font-size:16px;font-weight:500;text-transform:uppercase;margin-bottom:16px}
.foot-col li{list-style:none;font-size:13.5px;color:var(--text);line-height:26px}
.foot-col.contact li{display:flex;align-items:center;gap:9px;line-height:30px;font-size:12.5px;color:#333}
.copyright{left:0;width:1200px;top:3140px;text-align:center;font-size:12.5px;color:#333}
</style>
</head>
<body>

<div class="abs topbar">ACHIEVE YOUR DREAMS WITH OUR CUSTOM, TAILOR-MADE ABOVE-GROUND POOLS</div>

<div class="abs brand">BRISA<br>LAGOON</div>

<nav class="abs nav">
  <svg style="left:7px;top:11px" width="15" height="15" viewBox="0 0 16 16"><circle cx="6.5" cy="6.5" r="4.8" fill="none" stroke="#111" stroke-width="2.2"/><path d="M10 10l4.5 4.5" stroke="#111" stroke-width="2.6" stroke-linecap="round"/></svg>
  <div class="nav-links"><span>HOME</span><span>OUR PRODUCTS</span><span>OUR WORK</span><span>CONTACT US</span></div>
  <svg style="left:860px;top:12px" width="13" height="13" viewBox="0 0 14 14"><circle cx="7" cy="4" r="3.3" fill="#111"/><path d="M1 14c0-4 2.7-6 6-6s6 2 6 6z" fill="#111"/></svg>
  <svg style="left:893px;top:9px" width="22" height="22" viewBox="0 0 22 22"><circle cx="11" cy="11" r="10.5" fill="#d52b2b"/><path d="M1.5 8h19M1 12.5h20M2.5 17h17" stroke="#fff" stroke-width="2"/><path d="M11 .5A10.5 10.5 0 0 0 .5 11H11z" fill="#2a3d8f"/></svg>
</nav>

<div class="abs hero-photo" role="img" aria-label="Child in goggles splashing in an above-ground pool with a water volleyball net at sunset"></div>
<h1 class="abs hero-title">Transform your<br>garden with our<br>premium above-ground pools!</h1>
<div class="abs btn hero-btn">Our Product</div>
<div class="abs slide-next"><svg width="12" height="14" viewBox="0 0 12 14"><path d="M3 1.5l6 5.5-6 5.5" fill="none" stroke="#111" stroke-width="2"/></svg></div>

<div class="photo" style="left:0;top:730px;width:641px;height:398px;background:linear-gradient(180deg,#3f7a2c 0%,#6ca541 35%,#3fb5d6 50%,#b8693a 65%,#d49a78 100%)" role="img" aria-label="Round wooden-clad above-ground pool with ladder on a timber deck in a green garden"></div>
<section class="panel" style="left:653px;top:730px;width:434px;height:398px;background:var(--ice)">
  <h2>Achieve your dreams with our<br>custom, tailor-made<br>above-ground pools.</h2>
  <p>Imagine an exceptional relaxation and leisure space right in your own backyard. With our unparalleled expertise and commitment to excellence, we create above-ground pools that exceed all expectations.</p>
  <div class="btn">View More</div>
</section>

<section class="panel" style="left:113px;top:1137px;width:435px;height:399px;background:var(--mist)">
  <h2>Personalized services</h2>
  <p>We understand that every garden and client is unique. That's why we offer personalized services, from design to installation and after-sales support. Our team of experts is here to answer all your questions and guide you throughout your project.</p>
</section>
<div class="photo" style="left:558px;top:1137px;width:642px;height:399px;background:linear-gradient(150deg,#6a4a22 0%,#b68a4c 30%,#3aa3d8 60%,#1f86c8 100%)" role="img" aria-label="Two children laughing and splashing with swim rings in a sunlit pool"></div>

<div class="photo" style="left:0;top:1552px;width:641px;height:399px;background:linear-gradient(170deg,#f2c46a 0%,#c9843c 25%,#3d5a2a 45%,#4e86c4 70%,#2b5a8f 100%)" role="img" aria-label="Children playing water volleyball in an above-ground pool at golden hour"></div>
<section class="panel" style="left:653px;top:1552px;width:434px;height:399px;background:var(--ice)">
  <h2>Guaranteed satisfaction</h2>
  <p>our satisfaction is our top priority. We are committed to providing you with exceptional service and the highest quality products. Join our community of satisfied customers who are already enjoying their custom above-ground pools. <b>10-Year Warranty!</b></p>
</section>

<section class="abs contact-box">
  <h2 class="serif-head">Contact us today</h2>
  <p>Don't wait any longer to transform your garden into a wellness oasis. Contact us today to discover our range of customizable above-ground pools and get a tailored quote. Dive into a world of infinite possibilities with</p>
  <h3 class="serif-head">We bring your pool dreams to life!</h3>
</section>

<h2 class="abs why serif-head">Why choose us</h2>

<article class="card" style="left:111px">
  <div class="photo" style="background:linear-gradient(160deg,#5a4a3a 0%,#b58a5a 40%,#3f8fb0 75%,#2a6a88 100%)" role="img" aria-label="Girl with sunglasses and friends splashing in a pool"></div>
  <div class="badge"><svg width="30" height="30" viewBox="0 0 30 30"><circle cx="15" cy="15" r="12" fill="none" stroke="#555" stroke-width="1.3"/><circle cx="15" cy="15" r="8" fill="none" stroke="#555" stroke-width="1.3"/><path d="M11.5 15l2.5 2.5 4.5-5" fill="none" stroke="#555" stroke-width="1.5"/></svg></div>
  <h4>Superior quality</h4>
  <p>Each pool is constructed with high-quality materials, ensuring exceptional durability and strength</p>
</article>

<article class="card" style="left:442px">
  <div class="photo" style="background:linear-gradient(180deg,#4f8a5a 0%,#45b4e6 25%,#2c9bd8 65%,#8c9198 85%,#6f747a 100%)" role="img" aria-label="Round steel-frame above-ground pool with a child swimming"></div>
  <div class="badge"><svg width="30" height="30" viewBox="0 0 30 30"><path d="M8 11l3-4h8l3 4-7 11z" fill="none" stroke="#555" stroke-width="1.3" stroke-linejoin="round"/><path d="M8 11h14M12 11l3 11 3-11M11 7l1 4M19 7l-1 4" fill="none" stroke="#555" stroke-width="1.1"/></svg></div>
  <h4>Elegant design</h4>
  <p>Our pools come in a variety of styles and finishes, seamlessly blending into any garden setting</p>
</article>

<article class="card" style="left:771px">
  <div class="photo" style="background:linear-gradient(180deg,#e9d7a8 0%,#c9a07a 35%,#3d6f7a 65%,#4a4a4a 100%)" role="img" aria-label="Two women relaxing in a dark round above-ground pool on a terrace"></div>
  <div class="badge"><svg width="30" height="30" viewBox="0 0 30 30"><circle cx="15" cy="15" r="9" fill="none" stroke="#555" stroke-width="1.3" stroke-dasharray="3.5 1.6"/><circle cx="15" cy="15" r="6" fill="none" stroke="#555" stroke-width="1.2"/><path d="M12.5 15l2 2 3.5-4" fill="none" stroke="#555" stroke-width="1.4"/></svg></div>
  <h4>Easy installation</h4>
  <p>4.Enjoy your new oasis quickly with our simple and fast installation process.</p>
</article>

<div class="abs divider"></div>

<div class="abs foot-brand">BRISA<br>LAGOON</div>

<div class="abs foot-col" style="left:377px;top:2954px">
  <h5>Company</h5>
  <ul><li>About Us</li><li>Contact Us</li><li>Blog</li><li>Privacy Policy</li></ul>
</div>
<div class="abs foot-col" style="left:596px;top:2954px">
  <h5>Information</h5>
  <ul><li>FAQ's</li><li>Terms</li><li>Delivery Info</li><li>Refund policy</li><li>Size Guide</li></ul>
</div>
<div class="abs foot-col contact" style="left:909px;top:2954px">
  <h5>Contact us</h5>
  <ul>
    <li><svg width="9" height="12" viewBox="0 0 9 12"><path d="M4.5 0A4.5 4.5 0 0 0 0 4.5C0 8 4.5 12 4.5 12S9 8 9 4.5A4.5 4.5 0 0 0 4.5 0zm0 6.2a1.7 1.7 0 1 1 0-3.4 1.7 1.7 0 0 1 0 3.4z" fill="#555"/></svg>Lorum ipsum Dolot Sit Amet</li>
    <li><svg width="12" height="12" viewBox="0 0 12 12"><path d="M2.4 0l2 2.7-1.2 1.5a7 7 0 0 0 4.6 4.6l1.5-1.2L12 9.6 10.6 12C4.8 12 0 7.2 0 1.4z" fill="#555"/></svg>+41 21 555 01 42</li>
    <li><svg width="13" height="10" viewBox="0 0 13 10"><rect width="13" height="10" rx="1" fill="#555"/><path d="M.5 1l6 4.5 6-4.5" fill="none" stroke="#fff" stroke-width="1.2"/></svg>info@brisalagoon.com</li>
  </ul>
</div>

<div class="abs copyright">Copyright@2024 All Rights by Brisa Lagoon</div>

</body>
</html>
```